Business Card Design

I need a business card for a new company based in Australia called "MedLinkora".

Its a cloud program for GPs that allows them to search for the specialist they require using a simple user friendly tool.

I would like the colours to match those in the program (the colours in the logo attached).

The final design should reflect the programs clarity, ease of use and professionalism.

Target Market(s)

GPs and other Health Professionals

Industry/Entity Type

Business

Contact Information for Business Card

MedLinkora; The Whole Consultant Index; Marla Voss CEO; 0438215967; marla@medlinkora.example; www.medlinkora.example

Requirements
Must have
• Must have the logo attached; the web address and my name and phone number
Nice to have
• the slogan "The Whole Consultant Index"

```html
<!DOCTYPE html>
<html lang="en">
<head>
<meta charset="utf-8">
<title>MedLinkora Business Cards</title>
<link rel="stylesheet" href="https://fonts.googleapis.com/css2?family=Questrial&family=Open+Sans:wght@400;700&display=swap">
<style>
  :root {
    --bg: #e9e6e1;
    --card-dark: #050505;
    --brand-blue: #00b2e6;
    --white: #ffffff;
    --rule-grey: #8a8a8a;
    --soft-white: #eaf8fd;
  }
  * { box-sizing: border-box; margin: 0; padding: 0; }
  html, body {
    width: 1200px; height: 829px; overflow: hidden;
    background: var(--bg);
  }
  .canvas {
    position: relative; width: 1200px; height: 829px;
    display: flex; align-items: center; justify-content: center; gap: 50px;
  }
  .card {
    position: relative; width: 530px; height: 303px;
    overflow: hidden; border-radius: 3px;
    box-shadow: 0 6px 18px rgba(0,0,0,0.18);
  }

  /* Front: dark contact card */
  .card--front { background: var(--card-dark); color: var(--white); }
  .front__brand { position: absolute; left: 34px; top: 26px; }
  .brand-name {
    font-family: "Questrial", sans-serif; font-weight: 400;
    letter-spacing: -1px; line-height: 1;
  }
  .front__brand .brand-name { font-size: 52px; color: var(--brand-blue); }
  .brand-tagline {
    font-family: "Questrial", sans-serif; letter-spacing: 0.5px;
  }
  .front__brand .brand-tagline { font-size: 17px; color: #cfcfcf; margin-top: 2px; }

  .rule {
    position: absolute; left: 0; right: 0; height: 1px; background: var(--rule-grey);
  }
  .rule--top-a { top: 113px; }
  .rule--top-b { top: 144px; }
  .name-band {
    position: absolute; left: 0; right: 0; top: 117px; height: 24px;
    background: var(--brand-blue);
    font-family: "Open Sans", sans-serif; font-size: 16px; font-weight: 700;
    line-height: 24px; padding-left: 220px; color: var(--white);
  }
  .name-band .role { font-weight: 400; font-size: 12px; }

  .contact { font-family: "Open Sans", sans-serif; color: var(--white); }
  .contact__row { position: absolute; display: flex; align-items: center; gap: 7px; white-space: nowrap; }
  .contact__row svg { flex: none; }
  .contact__row--phone { left: 240px; top: 158px; font-size: 18px; }
  .contact__row--web { left: 240px; top: 191px; font-size: 12.5px; gap: 14px; }
  .contact__row--email { left: 62px; top: 242px; font-size: 12.5px; }
  .contact__item { display: flex; align-items: center; gap: 6px; }

  .rule--bottom-a { top: 227px; }
  .footer-band {
    position: absolute; left: 0; right: 0; top: 268px; height: 18px;
    background: var(--brand-blue);
  }
  .rule--bottom-b { top: 289px; }

  /* Back: blue logo card */
  .card--back {
    background: var(--brand-blue); color: var(--white);
    display: flex; flex-direction: column; align-items: center; justify-content: center;
  }
  .back__brand { text-align: left; }
  .card--back .brand-name { font-size: 66px; color: var(--white); }
  .card--back .brand-tagline { font-size: 20px; color: var(--white); margin-top: 2px; }
  .back__web {
    margin-top: 26px; font-family: "Open Sans", sans-serif; font-size: 17px;
    letter-spacing: 1.5px; color: var(--soft-white);
  }
</style>
</head>
<body>
<main class="canvas">

  <section class="card card--front" aria-label="Business card front">
    <div class="front__brand">
      <div class="brand-name">MedLinkora</div>
      <div class="brand-tagline">The Whole Consultant Index</div>
    </div>

    <div class="rule rule--top-a"></div>
    <div class="name-band">Marla Voss, <span class="role">CEO</span></div>
    <div class="rule rule--top-b"></div>

    <div class="contact">
      <div class="contact__row contact__row--phone">
        <svg width="18" height="18" viewBox="0 0 18 18" aria-hidden="true">
          <circle cx="9" cy="9" r="8.5" fill="var(--white)"/>
          <path d="M6 4.5c.5 0 .9.2 1 .6l.6 1.6c.1.3 0 .7-.3.9l-.6.5c.5 1.1 1.3 2 2.4 2.5l.5-.6c.2-.3.6-.4.9-.3l1.6.6c.4.1.6.5.6 1v1c0 .6-.5 1-1.1 1C8 13.1 4.9 10 4.7 5.6c0-.6.4-1.1 1-1.1z" fill="var(--card-dark)"/>
        </svg>
        <span>0438215967</span>
      </div>

      <div class="contact__row contact__row--web">
        <span class="contact__item">
          <svg width="13" height="13" viewBox="0 0 14 14" aria-hidden="true">
            <circle cx="7" cy="7" r="6.3" fill="none" stroke="var(--white)" stroke-width="1.3"/>
            <ellipse cx="7" cy="7" rx="2.6" ry="6.3" fill="none" stroke="var(--white)" stroke-width="1"/>
            <line x1="0.7" y1="7" x2="13.3" y2="7" stroke="var(--white)" stroke-width="1"/>
          </svg>
          www.medlinkora.example
        </span>
      </div>

      <div class="rule rule--bottom-a"></div>

      <div class="contact__row contact__row--email">
        <svg width="15" height="11" viewBox="0 0 15 11" aria-hidden="true">
          <rect x="0.5" y="0.5" width="14" height="10" rx="1" fill="var(--white)"/>
          <path d="M1 1l6.5 5 6.5-5" fill="none" stroke="var(--card-dark)" stroke-width="1.2"/>
        </svg>
        <span>marla@medlinkora.example</span>
      </div>
    </div>

    <div class="footer-band"></div>
    <div class="rule rule--bottom-b"></div>
  </section>

  <section class="card card--back" aria-label="Business card back">
    <div class="back__brand">
      <div class="brand-name">MedLinkora</div>
      <div class="brand-tagline">The Whole Consultant Index</div>
    </div>
    <div class="back__web">www.medlinkora.example</div>
  </section>

</main>
</body>
</html>
```